Brimlow Plumbing Solutions

This is for my new plumbing company, I have attached an example of what I’m going for but want it to look better.

Target Market(s)

Home owners, real estate, etc.

Industry/Entity Type

Plumbing

Font styles to use
Other font styles liked:
• As per my logo and other examples uploaded

Colors

Designer to choose colors to be used in the design.

Requirements
Must have
• Must include my logo provided and similar to my flyer I have attached but better

```html
<!DOCTYPE html>
<html lang="en">
<head>
<meta charset="utf-8">
<title>Brimlow Plumbing Solutions – Flyer</title>
<link rel="stylesheet" href="https://fonts.googleapis.com/css2?family=Montserrat:wght@400;500;600;700;800&display=swap">
<style>
  :root {
    --backdrop: #9dbfdc;
    --paper: #ffffff;
    --navy: #13294b;
    --navy-deep: #0f2443;
    --mid-blue: #4d76a5;
    --tile-line: #a9c3df;
    --sky: #9bbede;
    --orange: #f0842c;
    --ink-light: #ffffff;
    --ink-soft: #e4edf7;
  }
  * { box-sizing: border-box; margin: 0; padding: 0; }
  html, body {
    width: 1200px; height: 1200px; overflow: hidden;
    background: var(--backdrop);
    font-family: "Montserrat", sans-serif;
  }
  .flyer {
    position: absolute; left: 268px; top: 98px;
    width: 664px; height: 1004px;
    background: var(--paper);
    overflow: hidden;
  }
  .brand {
    position: absolute; top: 40px; left: 0; width: 100%;
    text-align: center; color: var(--navy);
  }
  .brand-name { font-size: 32px; font-weight: 800; letter-spacing: 0.5px; line-height: 1; }
  .brand-sub { font-size: 11px; font-weight: 700; letter-spacing: 0.3px; margin-top: 8px; }

  .shapes { position: absolute; inset: 0; }

  .wave-field {
    position: absolute; left: 0; top: 426px; width: 664px; height: 439px;
    background: radial-gradient(ellipse at 85% 10%, rgba(160,190,225,0.45), rgba(77,118,165,0) 60%),
                radial-gradient(ellipse at 20% 85%, rgba(120,155,200,0.35), rgba(77,118,165,0) 55%);
  }

  .headline {
    position: absolute; left: 47px; top: 184px;
    color: var(--ink-light); font-size: 37px; font-weight: 600; line-height: 1.18;
  }
  .tagline {
    position: absolute; left: 47px; top: 290px;
    color: var(--ink-light); font-size: 21px; font-weight: 500; line-height: 1.3;
  }
  .discount {
    position: absolute; left: 508px; top: 299px; width: 98px; height: 98px;
    border-radius: 50%; background: var(--orange);
    color: var(--ink-light); font-size: 16px; font-weight: 500; line-height: 1.2;
    display: flex; flex-direction: column; align-items: center; justify-content: center; text-align: center;
  }
  .discount-value { font-weight: 700; }
  .services-title {
    position: absolute; left: 47px; top: 383px;
    color: var(--ink-light); font-size: 25px; font-weight: 600;
  }
  .services-intro {
    position: absolute; left: 47px; top: 442px;
    color: var(--ink-soft); font-size: 16px; font-weight: 500; line-height: 1.45;
  }
  .service-grid {
    position: absolute; left: 47px; top: 502px;
    display: grid; grid-template-columns: repeat(4, 135px); grid-auto-rows: 164px;
    column-gap: 11px; row-gap: 13px;
  }
  .service-tile {
    border: 1.5px solid var(--tile-line);
    background: rgba(30,60,105,0.35);
    display: flex; flex-direction: column; align-items: center;
    padding: 28px 8px 0; color: var(--ink-light); text-align: center;
    font-size: 14px; font-weight: 500; line-height: 1.35;
  }
  .service-icon {
    width: 36px; height: 36px; margin-bottom: 18px;
    border: 1.5px solid var(--ink-soft); border-radius: 6px; opacity: 0.85;
  }

  .footer {
    position: absolute; left: 0; top: 900px; width: 100%; height: 104px;
    display: flex; align-items: center; padding-left: 40px;
    color: var(--navy); font-size: 13px; font-weight: 500;
  }
  .contact { display: flex; align-items: center; gap: 9px; }
  .contact-phone { width: 212px; line-height: 1.3; }
  .contact-web { width: 150px; }
  .contact-mail { width: 128px; }
  .socials { display: flex; gap: 9px; }
  .social-dot { width: 21px; height: 21px; border-radius: 50%; background: var(--navy); }
</style>
</head>
<body>
<main class="flyer">
  <header class="brand">
    <div class="brand-name">BRIMLOW</div>
    <div class="brand-sub">PLUMBING SOLUTIONS</div>
  </header>

  <svg class="shapes" width="664" height="1004" viewBox="0 0 664 1004" aria-hidden="true">
    <rect x="0" y="137" width="432" height="4" fill="var(--orange)"/>
    <rect x="432" y="133" width="232" height="25" fill="var(--sky)"/>
    <rect x="0" y="383" width="664" height="482" fill="var(--mid-blue)"/>
    <polygon points="0,158 664,158 664,383 330,383 284,424 0,424" fill="var(--navy)"/>
    <line x1="330" y1="384" x2="664" y2="384" stroke="var(--sky)" stroke-width="3"/>
    <line x1="284" y1="425" x2="0" y2="425" stroke="#6f93bd" stroke-width="2"/>
    <rect x="0" y="865" width="225" height="35" fill="var(--sky)"/>
    <rect x="225" y="879" width="209" height="5" fill="var(--orange)"/>
    <rect x="434" y="865" width="230" height="28" fill="var(--navy-deep)"/>
  </svg>

  <div class="wave-field" role="img" aria-label="Soft flowing water wave texture"></div>

  <h1 class="headline">Your Local Reliable<br>Sydney Plumber</h1>
  <p class="tagline">Specialising in Plumbing, Drainage<br>&amp; Gas Maintenance.</p>
  <div class="discount"><span>Discount</span><span class="discount-value">10% OFF</span></div>

  <h2 class="services-title">Our Services</h2>
  <p class="services-intro">Reliable Plumbing,<br>Real Solutions</p>

  <section class="service-grid">
    <div class="service-tile"><div class="service-icon" role="img" aria-label="Emergency tool icon"></div>Emergency<br>Plumbing &amp;<br>Repairs</div>
    <div class="service-tile"><div class="service-icon" role="img" aria-label="Tap icon"></div>Blocked<br>Drains</div>
    <div class="service-tile"><div class="service-icon" role="img" aria-label="Pipe fitting icon"></div>Hot Water<br>Systems</div>
    <div class="service-tile"><div class="service-icon" role="img" aria-label="Appliance icon"></div>Gas<br>Fitting</div>
    <div class="service-tile"><div class="service-icon" role="img" aria-label="Crossed tools icon"></div>Service<br>Plumbing</div>
    <div class="service-tile"><div class="service-icon" role="img" aria-label="Wrench icon"></div>Leak<br>Detection</div>
    <div class="service-tile"><div class="service-icon" role="img" aria-label="Water heater icon"></div>Bathroom<br>Renovations</div>
  </section>

  <footer class="footer">
    <div class="contact contact-phone">
      <svg width="20" height="20" viewBox="0 0 24 24" aria-hidden="true"><path fill="var(--navy)" d="M6.6 10.8a15.1 15.1 0 0 0 6.6 6.6l2.2-2.2a1 1 0 0 1 1-.25 11.4 11.4 0 0 0 3.6.57 1 1 0 0 1 1 1V20a1 1 0 0 1-1 1A17 17 0 0 1 3 4a1 1 0 0 1 1-1h3.5a1 1 0 0 1 1 1c0 1.25.2 2.45.57 3.6a1 1 0 0 1-.25 1z"/></svg>
      <span>Call Us Today<br>0400 000 000</span>
    </div>
    <div class="contact contact-web">
      <svg width="18" height="18" viewBox="0 0 24 24" aria-hidden="true"><circle cx="12" cy="12" r="10" fill="none" stroke="var(--navy)" stroke-width="2.4"/><path d="M2 12h20M12 2c3 3 3 17 0 20M12 2c-3 3-3 17 0 20" fill="none" stroke="var(--navy)" stroke-width="2"/></svg>
      <span>brimlow.com.au</span>
    </div>
    <div class="contact contact-mail">
      <svg width="20" height="16" viewBox="0 0 24 18" aria-hidden="true"><rect x="1" y="1" width="22" height="16" fill="none" stroke="var(--navy)" stroke-width="2"/><path d="M1 1l11 9 11-9" fill="none" stroke="var(--navy)" stroke-width="2"/></svg>
      <span>Email us</span>
    </div>
    <div class="socials" aria-label="Social media">
      <span class="social-dot"></span><span class="social-dot"></span><span class="social-dot"></span>
    </div>
  </footer>
</main>
</body>
</html>
```